Digital Marketing Website Redesign, modern, fresh, dynamic

Hi there, we would like to freshen up our website and create a new dynamic look. We are a digital marketing agency who specialise in digital transformation in the form of creating websites for appointment bookings. Our clients are service businesses such as hairdressers, dentists and doctors who's patients need to book appointments with them.

Our company name is Tallomex with the point being we can help increase your revenue curve by increasing your appointment bookings.

Our services include building the website, creating campaigns to drive traffic, increasing conversions and monitoring and reporting.

We are playing with a tagline of 'Step into your Digital Transformation' as we have a 5 step journey that customers can take with us getting them from zero to full appointment bookings.

Our current website is www.tallomex-sample.com

You can see a draft design that I mocked up on Canva here https://www.draftboard-sample.com/design/QXB82LmpR7T/KpoW39dnFsYbZet_wqe_OPa/edit?utm_content=QXB82LmpR7T&utm_campaign=designshare&utm_medium=link2&utm_source=sharebutton

Also attached some other homepage ideas. In regard to photos we are open to ideas.

Please let if you need any more information to provide us with an initial design. Thanks million and I look forward to receiving fantastic designs :)

Marian Dobbs
Tallomex

Target Market(s)

Appointment based businesses such as hairdressers, dentists, doctors

Industry/Entity Type

Marketing and Digital

Coding

Coded - Design and coding required

Number of Pages Required

1 page

Colors
0094D4
00A9DD
6FCCEA
C7EBF8
E9F6FB

Requirements
Must have
• Appointment booking CTA
Nice to have
• A website we like https://www.fergalwhitty-sample.ie

```html
<!DOCTYPE html>
<html lang="en">
<head>
<meta charset="utf-8">
<title>Tallomex – Digital Marketing</title>
<link href="https://fonts.googleapis.com/css2?family=Open+Sans:wght@400;500;600;700&display=swap" rel="stylesheet">
<style>
:root{
  --navy:#1f3468;
  --navy-deep:#141c3a;
  --navy-bar:#262e4c;
  --lime:#c4d000;
  --lime-soft:#eef3c2;
  --orange:#f08a1c;
  --text:#6b7280;
  --ink:#1d2b55;
  --line:#d9dde6;
  --grey-bg:#f4f5f7;
  --sky:#0094d4;
  --sky-pale:#e9f6fb;
}
*{margin:0;padding:0;box-sizing:border-box}
html,body{width:1200px;height:5220px;overflow:hidden}
body{position:relative;font-family:"Open Sans",sans-serif;color:var(--text);background:#fff}
.abs{position:absolute}
section,header,footer{position:absolute;left:0;width:1200px}
.center{text-align:center;left:0;width:1200px}

/* header */
.site-header{top:0;height:126px;background:#fff}
.contact-chip{top:22px;display:flex;align-items:center;gap:12px;font-size:12px;color:var(--ink)}
.contact-chip .dot{width:30px;height:30px;border-radius:50%;background:var(--navy);display:flex;align-items:center;justify-content:center}
.contact-chip b{display:block;font-weight:600;font-size:12px}
.contact-chip span{font-size:10px;color:var(--text)}
.brand{font-weight:700;color:var(--navy);font-size:40px;display:flex;align-items:center;gap:10px;white-space:nowrap}
.brand .mark{width:16px;height:16px;border-radius:50%;background:var(--lime)}
.btn-appoint{top:14px;left:880px;width:182px;height:39px;border-radius:20px;background:var(--navy);color:#fff;font-size:12px;font-weight:600;display:flex;align-items:center;justify-content:center}
.nav a{position:absolute;top:89px;font-size:12px;color:var(--ink);text-decoration:none}
.nav-line{top:72px;left:700px;width:362px;height:1px;background:var(--line)}

/* hero */
.hero{top:126px;height:800px;background:radial-gradient(ellipse at 58% 62%,#5aa9c9 0%,#1f5f86 18%,#10304e 45%,#0a1628 80%);overflow:hidden}
.hero-kicker{top:362px;left:81px;color:#fff;font-size:24px;letter-spacing:4px;font-weight:500}
.hero-title{top:410px;left:79px;color:#fff;font-size:52px;font-weight:600;line-height:70px}
.hero-rule{top:495px;left:81px;width:722px;height:1px;background:rgba(255,255,255,.5)}
.hero-copy{top:528px;left:81px;width:620px;color:#fff;font-size:15px;line-height:27px;font-weight:500}
.btn{position:absolute;height:39px;border-radius:20px;font-size:14px;font-weight:600;display:flex;align-items:center;justify-content:center}
.btn-lime{background:var(--lime);color:#fff}
.btn-white{background:#fff;color:var(--ink)}
.swoosh{top:830px;left:0}

/* feature cards */
.feature{top:805px;width:320px;height:283px;background:#fff;border-radius:6px;box-shadow:0 6px 22px rgba(20,30,60,.12);text-align:center}
.feature .icon{position:absolute;top:32px;left:120px;width:80px;height:70px}
.feature h3{position:absolute;top:128px;width:100%;color:var(--navy);font-size:19px;font-weight:500}
.feature p{position:absolute;top:166px;left:40px;width:240px;font-size:13px;line-height:26px}

/* about */
.label{font-size:11px;font-weight:700;color:var(--lime);letter-spacing:.5px}
.about-title{top:1200px;left:101px;width:460px;color:var(--navy);font-size:35px;line-height:53px;font-weight:600}
.about-copy{top:1318px;left:101px;width:420px;font-size:13px;line-height:24.8px}
.btn-square{position:absolute;top:1549px;left:101px;width:153px;height:44px;background:var(--lime);color:#fff;font-weight:600;font-size:15px;display:flex;align-items:center;justify-content:center;gap:12px;border-radius:2px}
.photo{border-radius:4px}

/* services */
.services{top:1666px;height:655px;background:var(--grey-bg)}
.section-title{font-size:35px;font-weight:600;color:var(--navy)}
.section-copy{font-size:13px;line-height:24px}
.svc-card{top:260px;width:320px;height:287px;border-radius:6px}
.svc-pill{top:523px;height:50px;background:#fff;border-radius:4px;box-shadow:0 4px 14px rgba(0,0,0,.1);color:var(--navy);font-weight:600;font-size:15px;display:flex;align-items:center;justify-content:center}

/* band */
.band{top:2321px;height:308px;background:linear-gradient(120deg,#0f2a5c 0%,#1b3f86 40%,#12306a 70%,#0a1c45 100%)}
.band h2{top:108px;color:#fff;font-size:34px;font-weight:500;line-height:42px}
.band h2 em{font-style:normal;color:var(--lime)}
.band-pill{top:2597px;left:351px;width:500px;height:54px;background:#fff;border-radius:4px;box-shadow:0 6px 20px rgba(0,0,0,.12);display:flex;align-items:center;justify-content:space-around;font-size:16px;color:var(--ink);font-weight:500;padding:0 20px}

/* reviews */
.review{top:2899px;width:326px;height:318px;background:#fff;box-shadow:0 4px 18px rgba(20,30,60,.1);text-align:center}
.avatar{position:absolute;top:-33px;left:130px;width:66px;height:66px;border-radius:50%;border:4px solid #fff;box-shadow:0 2px 8px rgba(0,0,0,.15)}
.stars{position:absolute;top:60px;width:100%;color:var(--orange);font-size:20px;letter-spacing:9px}
.review p{position:absolute;top:102px;left:50px;width:226px;font-size:13px;line-height:25px}
.quote{position:absolute;top:233px;left:128px}
.reviewer{top:3192px;width:326px;text-align:center}
.reviewer b{display:block;font-size:17px;color:var(--ink);font-weight:600}
.reviewer span{font-size:12px}

/* why */
.why{top:3300px;height:602px;background:linear-gradient(100deg,#1a3f70 0%,#2d6aa0 35%,#8fb1cc 65%,#4f6f8e 100%)}
.why-card{top:65px;left:91px;width:509px;height:466px;background:#fff;border-radius:8px}
.why-card h2{position:absolute;top:84px;left:51px;font-size:35px;color:var(--navy);font-weight:600}
.why-item{position:absolute;left:51px;width:420px}
.why-item b{position:absolute;left:58px;top:0;font-size:12px;color:var(--navy);font-weight:700}
.why-item p{position:absolute;left:58px;top:22px;width:350px;font-size:12.5px;line-height:25px}

/* form */
.form-card{top:4119px;left:138px;width:914px;height:474px;background:#fff;border-radius:10px;box-shadow:0 4px 26px rgba(20,30,60,.1)}
.field{position:absolute;border:1.5px solid var(--navy);border-radius:22px;height:42px}
.field label{position:absolute;top:-10px;left:30px;background:#fff;padding:0 6px;font-size:12px;color:var(--ink);font-weight:500}
.field span{position:absolute;top:14px;left:34px;font-size:12px;font-style:italic;color:#8a93a8}
.field.active{background:var(--sky-pale)}
.field.active label{background:transparent}
.soc{position:absolute;top:4515px;width:30px;height:30px;border-radius:50%;border:1.5px solid var(--navy);display:flex;align-items:center;justify-content:center}
.soc i{width:8px;height:8px;border-radius:50%;background:var(--navy)}
.btn-submit{position:absolute;top:4510px;left:843px;width:142px;height:41px;border-radius:21px;background:var(--lime);color:#fff;font-size:13px;font-weight:600;display:flex;align-items:center;justify-content:space-between;padding:0 8px 0 36px}

/* footer */
.footer{top:4662px;height:498px;background:var(--navy-deep)}
.sq{position:absolute;top:100px;width:36px;height:36px;border-radius:3px}
.go-top{top:109px;left:987px;color:#fff;font-size:14px;font-weight:600}
.go-top-btn{top:96px;left:1072px;width:43px;height:43px;background:var(--lime);border-radius:3px}
.footer-rule{top:174px;left:81px;width:1034px;height:1px;background:rgba(255,255,255,.3)}
.footer h2{top:236px;color:#fff;font-size:26px;font-weight:600}
.footer .tag{top:290px;color:#fff;font-size:15px;line-height:25px}
.fcontact{position:absolute;top:380px;display:flex;gap:14px;align-items:center;color:#fff}
.fcontact small{display:block;font-size:14px;color:#cfd4e2}
.fcontact b{font-size:16px;font-weight:700}
.fdiv{position:absolute;top:374px;width:1px;height:60px;background:rgba(255,255,255,.35)}
.bottom-bar{top:5160px;height:60px;background:var(--navy-bar);color:#fff;font-size:12px;font-weight:600}
.bottom-bar span{position:absolute;top:22px}
</style>
</head>
<body>

<header class="site-header">
  <div class="abs contact-chip" style="left:122px">
    <div class="dot"><svg width="14" height="14" viewBox="0 0 24 24" fill="#fff"><path d="M6.6 10.8a15 15 0 006.6 6.6l2.2-2.2a1 1 0 011-.25 11.4 11.4 0 003.6.57 1 1 0 011 1V20a1 1 0 01-1 1A17 17 0 013 4a1 1 0 011-1h3.5a1 1 0 011 1c0 1.25.2 2.45.57 3.57a1 1 0 01-.25 1z"/></svg></div>
    <div><b>Call Us</b><span>02(55)01 7720</span></div>
  </div>
  <div class="abs contact-chip" style="left:281px">
    <div class="dot"><svg width="14" height="14" viewBox="0 0 24 24" fill="none" stroke="#fff" stroke-width="2"><rect x="3" y="5" width="18" height="14"/><path d="M3 5l9 7 9-7"/></svg></div>
    <div><b>Email:</b><span>office@tallomex-sample.com</span></div>
  </div>
  <div class="abs brand" style="left:492px;top:38px"><span class="mark"></span>Tallomex</div>
  <div class="abs btn-appoint">MAKE APPOINTMENT</div>
  <div class="abs nav-line"></div>
  <nav class="nav">
    <a style="left:124px">Home</a><a style="left:236px">About Us</a><a style="left:386px">Services</a>
    <a style="left:704px">Our team</a><a style="left:832px">Projects</a><a style="left:957px">Contact Us</a>
  </nav>
</header>

<section class="hero" role="img" aria-label="Businessman walking down a glowing digital circuit corridor">
  <div class="abs" style="left:450px;top:150px;width:360px;height:640px;background:radial-gradient(ellipse at 50% 60%,rgba(130,200,230,.35),transparent 65%)"></div>
</section>
<div class="abs hero-kicker">DIGITAL MARKETING</div>
<div class="abs hero-title">Digital Transformation</div>
<div class="abs hero-rule"></div>
<p class="abs hero-copy">Lorem ipsum dolor sit amet, consectetur adipiscing elit et dolore conser tempor<br>incididunt ut labore et dolore magna</p>
<div class="btn btn-lime" style="top:614px;left:81px;width:142px">LEARN MORE</div>
<div class="btn btn-white" style="top:614px;left:239px;width:213px">MAKE APPOINTMENT</div>

<svg class="abs swoosh" width="1200" height="130" viewBox="0 0 1200 130">
  <path d="M0 30 C400 40 800 60 1200 70 L1200 130 L0 130Z" fill="#fff"/>
  <path d="M0 28 C400 38 800 58 1200 68 L1200 92 C800 80 400 62 0 62Z" fill="#1f3468"/>
  <path d="M0 62 C400 66 800 82 1200 92 L1200 110 C800 100 400 90 0 108Z" fill="#c4d000"/>
</svg>

<div class="abs feature" style="left:91px">
  <svg class="icon" viewBox="0 0 80 70"><circle cx="34" cy="30" r="24" fill="var(--lime-soft)"/><path d="M30 56h26M38 56l4-14 8-10 4 3-8 10-8 11" fill="none" stroke="#c4d000" stroke-width="2.5"/><circle cx="44" cy="24" r="4" fill="none" stroke="#c4d000" stroke-width="2.5"/></svg>
  <h3>Expertise</h3><p>Lorem ipsum dolor sit amet, consect adipiscing elit, sed do eiusmod tempor incididunt ut labore et dolore</p>
</div>
<div class="abs feature" style="left:442px">
  <svg class="icon" viewBox="0 0 80 70"><circle cx="34" cy="30" r="24" fill="var(--lime-soft)"/><path d="M28 54a16 16 0 1124 0" fill="none" stroke="#c4d000" stroke-width="2.5"/><path d="M40 46l6-12" stroke="#c4d000" stroke-width="2.5"/><circle cx="40" cy="46" r="3" fill="#c4d000"/></svg>
  <h3>Professional</h3><p>Lorem ipsum dolor sit amet, consect adipiscing elit, sed do eiusmod tempor incididunt ut labore et dolore</p>
</div>
<div class="abs feature" style="left:786px">
  <svg class="icon" viewBox="0 0 80 70"><circle cx="34" cy="30" r="24" fill="var(--lime-soft)"/><path d="M44 18l5 10 11 2-8 8 2 11-10-5-10 5 2-11-8-8 11-2z" fill="none" stroke="#c4d000" stroke-width="2.5"/></svg>
  <h3>Experience</h3><p>Lorem ipsum dolor sit amet, consect adipiscing elit, sed do eiusmod tempor incididunt ut labore et dolore</p>
</div>

<!-- about -->
<div class="abs label" style="top:1181px;left:101px">ABOUT US &nbsp;&nbsp; —</div>
<h2 class="abs about-title">Where Ideas Meet Impact in the Digital Realm</h2>
<p class="abs about-copy">Lorem ipsum dolor sit amet, consectetur adipiscing elit, sed do eius od tempor incididunt ut labore et dolore magna aliqua. Ut enim ad minim veniam, quis nostrud exercitation ullamco laboris nisi ut ali quip ex ea commodo consequat. Duis aute irure dolor in re prehenderit in voluptate velit esse cillum dolore eu fugiat nulla pariatur. Excepteur sint occaecat cupidatat non proident, sunt in culpa qui officia deserunt mollit anim id est laborum pariatur. Exce pteur sint occaecat cupidatat non proident, sunt in culpa qui</p>
<div class="btn-square">Learn More <span>→</span></div>
<div class="abs photo" style="top:1186px;left:608px;width:497px;height:405px;background:linear-gradient(135deg,#f1f2ee 0%,#d9d6cf 45%,#a88f78 70%,#e8e6e1 100%)" role="img" aria-label="Smiling professional woman holding a tablet in a bright office"></div>
<svg class="abs" style="top:1310px;left:543px" width="120" height="120" viewBox="0 0 120 120">
  <circle cx="60" cy="60" r="56" fill="none" stroke="#b9bec9" stroke-width="1.5" stroke-dasharray="4 4"/>
  <circle cx="60" cy="60" r="36" fill="#fff" stroke="#e5e7ec"/>
  <text x="60" y="64" text-anchor="middle" font-family="Open Sans, sans-serif" font-size="11" font-weight="700" fill="#1f3468">Tallomex</text>
</svg>

<!-- services -->
<section class="services">
  <div class="abs center label" style="top:81px">—&nbsp; OUR SERVICES &nbsp;—</div>
  <h2 class="abs center section-title" style="top:104px">Our Services</h2>
  <p class="abs section-copy" style="top:167px;left:300px;width:600px;text-align:center">Lorem ipsum dolor sit amet, consectetur adipiscing elit, sed do eiusod tempor incididunt ut la bore et dolore magna aliqua. Ut enim ad minim veniam, quis nostrud exercitation</p>
  <div class="abs svc-card" style="left:93px;background:linear-gradient(135deg,#e4e8ee,#9aa4b3 60%,#4d5666)" role="img" aria-label="Hands typing on a laptop with cloud and data icons overlay"></div>
  <div class="abs svc-card" style="left:442px;background:linear-gradient(135deg,#cfd3d8,#6e7480 55%,#2d323a)" role="img" aria-label="Team reviewing work at a computer screen"></div>
  <div class="abs svc-card" style="left:788px;background:radial-gradient(circle at 55% 45%,#7fa8c8,#22344d 55%,#11161f)" role="img" aria-label="Hand holding a glowing digital globe"></div>
  <div class="abs svc-pill" style="left:152px;width:200px">Marketing Services</div>
  <div class="abs svc-pill" style="left:502px;width:204px">Online Booking Apps</div>
  <div class="abs svc-pill" style="left:846px;width:200px">Services Marketing</div>
</section>

<!-- band -->
<section class="band" role="img" aria-label="Abstract blue digital network background">
  <h2 class="abs center">We are available <em>24/7</em> to attend to your<br>Digital Marketing needs</h2>
</section>
<div class="abs band-pill"><span>+ (001) 555-014-220</span><span>[or]</span><span>hello@tallomex-sample.com</span></div>

<!-- reviews -->
<div class="abs center label" style="top:2690px">—&nbsp; TESTIMONIALS &nbsp;—</div>
<h2 class="abs center section-title" style="top:2713px">Client Reviews</h2>
<p class="abs section-copy" style="top:2773px;left:300px;width:600px;text-align:center">Lorem ipsum dolor sit amet, consectetur adipiscing elit, sed do eiusod tempor incididunt ut la bore et dolore magna aliqua. Ut enim ad minim veniam, quis nostrud exercitation</p>

<div class="abs review" style="left:91px">
  <div class="avatar" style="background:linear-gradient(#e9d6c4,#5a7aa8)" role="img" aria-label="Client portrait"></div>
  <div class="stars">★★★★★</div>
  <p>Lorem ipsum dolor sit amet, consectetur adipiscing elit, sed do eiusmod tempor incididunt ut labore et dolore</p>
  <svg class="quote" width="70" height="36" viewBox="0 0 70 36"><path d="M0 36a35 35 0 0170 0z" fill="var(--navy)"/><text x="35" y="30" text-anchor="middle" fill="#fff" font-size="26" font-weight="700" font-family="Open Sans, sans-serif">“</text></svg>
</div>
<div class="abs review" style="left:442px">
  <div class="avatar" style="background:linear-gradient(#f3c3c3,#c46a6a)" role="img" aria-label="Client portrait"></div>
  <div class="stars">★★★★★</div>
  <p>Lorem ipsum dolor sit amet, consectetur adipiscing elit, sed do eiusmod tempor incididunt ut labore et dolore</p>
  <svg class="quote" width="70" height="36" viewBox="0 0 70 36"><path d="M0 36a35 35 0 0170 0z" fill="var(--navy)"/><text x="35" y="30" text-anchor="middle" fill="#fff" font-size="26" font-weight="700" font-family="Open Sans, sans-serif">“</text></svg>
</div>
<div class="abs review" style="left:793px">
  <div class="avatar" style="background:linear-gradient(#f4f4f4,#d8cfc8)" role="img" aria-label="Client portrait"></div>
  <div class="stars">★★★★★</div>
  <p>Lorem ipsum dolor sit amet, consectetur adipiscing elit, sed do eiusmod tempor incididunt ut labore et dolore</p>
  <svg class="quote" width="70" height="36" viewBox="0 0 70 36"><path d="M0 36a35 35 0 0170 0z" fill="var(--navy)"/><text x="35" y="30" text-anchor="middle" fill="#fff" font-size="26" font-weight="700" font-family="Open Sans, sans-serif">“</text></svg>
</div>
<div class="abs reviewer" style="left:91px"><b>Rowan Pike</b><span>Country</span></div>
<div class="abs reviewer" style="left:442px"><b>Rowan Pike</b><span>Country</span></div>
<div class="abs reviewer" style="left:793px"><b>Rowan Pike</b><span>Country</span></div>

<!-- why -->
<section class="why" role="img" aria-label="Hands typing on a laptop surrounded by floating analytics charts">
  <div class="abs why-card">
    <div class="abs label" style="top:58px;left:51px">WHY CHOOSE US &nbsp;&nbsp; —</div>
    <h2>Empower. Transform.</h2>
    <div class="why-item" style="top:158px">
      <svg class="abs" style="left:0;top:2px" width="34" height="34" viewBox="0 0 34 34"><path d="M4 30h24M10 30l4-12 8-8 4 3-8 8-6 9" fill="none" stroke="#c4d000" stroke-width="2"/></svg>
      <b>Personalized Approach</b><p>Lorem ipsum dolor sit amet, consectetur adipiscing elit, od tempor incididunt ut labore et dolore magna</p>
    </div>
    <div class="why-item" style="top:251px">
      <svg class="abs" style="left:0;top:2px" width="34" height="34" viewBox="0 0 34 34"><path d="M17 3l4 9 10 1-7 7 2 10-9-5-9 5 2-10-7-7 10-1z" fill="none" stroke="#c4d000" stroke-width="2"/></svg>
      <b>Proven Track Record</b><p>Lorem ipsum dolor sit amet, consectetur adipiscing elit, od tempor incididunt ut labore et dolore magna</p>
    </div>
    <div class="why-item" style="top:342px">
      <svg class="abs" style="left:0;top:2px" width="34" height="34" viewBox="0 0 34 34"><path d="M7 28a13 13 0 1120 0" fill="none" stroke="#c4d000" stroke-width="2"/><path d="M17 22l5-9" stroke="#c4d000" stroke-width="2"/></svg>
      <b>Quality Services</b><p>Lorem ipsum dolor sit amet, consectetur adipiscing elit, od tempor incididunt ut labore et dolore magna</p>
    </div>
  </div>
</section>

<!-- form -->
<div class="abs center label" style="top:3953px">—&nbsp;&nbsp; OUR FORM &nbsp;&nbsp;—</div>
<h2 class="abs center section-title" style="top:3976px">Get in touch with us</h2>
<p class="abs section-copy" style="top:4036px;left:300px;width:600px;text-align:center">Lorem ipsum dolor sit amet, consectetur adipiscing elit, sed do eiusod tempor incididunt ut la bore et dolore magna aliqua. Ut enim ad minim veniam, quis nostrud exercitation</p>
<div class="abs form-card"></div>
<div class="field active" style="top:4180px;left:193px;width:391px"><label>First Name</label><span>Type Name</span></div>
<div class="field" style="top:4180px;left:606px;width:391px"><label>Last Name</label><span>Type Name</span></div>
<div class="field" style="top:4255px;left:193px;width:391px"><label>Telephone</label><span>123 456 789</span></div>
<div class="field" style="top:4255px;left:606px;width:391px"><label>Your Email</label><span>info@tallomex-sample.com</span></div>
<div class="field" style="top:4332px;left:193px;width:804px;height:148px;border-radius:14px"><label>Your Message</label><span>Type Message</span></div>
<div class="soc" style="left:207px"><i></i></div>
<div class="soc" style="left:245px"><i></i></div>
<div class="soc" style="left:284px"><i></i></div>
<div class="soc" style="left:322px"><i></i></div>
<div class="btn-submit">Submit <svg width="26" height="26" viewBox="0 0 26 26"><circle cx="13" cy="13" r="13" fill="#fff"/><path d="M11 8l5 5-5 5" fill="none" stroke="#c4d000" stroke-width="2"/></svg></div>

<!-- footer -->
<footer class="footer">
  <div class="sq" style="left:87px;background:#3b5998"></div>
  <div class="sq" style="left:136px;background:#2a6fb0"></div>
  <div class="sq" style="left:187px;background:#1da1f2"></div>
  <div class="sq" style="left:236px;background:#e02020"></div>
  <div class="abs brand" style="left:490px;top:90px;color:#2e6fb6"><span class="mark"></span>Tallomex</div>
  <div class="abs go-top">Go to top</div>
  <svg class="abs go-top-btn" viewBox="0 0 43 43"><rect width="43" height="43" fill="#c4d000"/><path d="M14 25l7.5-7.5L29 25" fill="none" stroke="#fff" stroke-width="3"/></svg>
  <div class="abs footer-rule"></div>
  <h2 class="abs center">Elevate Your Life, Elevate Your Mind</h2>
  <p class="abs tag" style="left:300px;width:600px;text-align:center">Lorem ipsum dolor sit amet, consectetur adipiscing elit, sed do eiusod tempor incididunt ut labore et dolore magna aliqua.</p>
  <div class="fcontact" style="left:235px">
    <svg width="38" height="44" viewBox="0 0 38 44" fill="none" stroke="#c4d000" stroke-width="2"><rect x="8" y="2" width="20" height="40" rx="3"/><path d="M15 36h6M32 14a8 8 0 010 12"/></svg>
    <div><small>Call Us</small><b>+1-555-014-2210</b></div>
  </div>
  <div class="fdiv" style="left:438px"></div>
  <div class="fcontact" style="left:476px">
    <svg width="48" height="44" viewBox="0 0 48 44" fill="none" stroke="#c4d000" stroke-width="2"><rect x="2" y="12" width="44" height="30"/><path d="M2 12l22 16 22-16M10 12V2h28v10"/></svg>
    <div><small>Mail Us</small><b>info@tallomex-sample.com</b></div>
  </div>
  <div class="fdiv" style="left:728px"></div>
  <div class="fcontact" style="left:760px">
    <svg width="44" height="44" viewBox="0 0 44 44" fill="none" stroke="#c4d000" stroke-width="2"><path d="M22 30s-10-10-10-17a10 10 0 0120 0c0 7-10 17-10 17z"/><circle cx="22" cy="13" r="4"/><path d="M8 30l-6 12h40l-6-12"/></svg>
    <div><small>Location</small><b>48 Harbour View Rd</b></div>
  </div>
</footer>

<div class="bottom-bar" style="position:absolute;left:0;width:1200px">
  <span style="left:85px">Tallomex</span>
  <span style="left:690px">Privacy</span>
  <span style="left:833px">Cookies Policy</span>
  <span style="left:1013px">Site Map</span>
</div>

</body>
</html>
```